Quellbrook Market Counsel needs an email sign off and professional power point template

Newly formed company and we require:1. graphic email signature on our email , and2.a professional powerpoint template (title page and sub pages) and revamp of the attached powerpoint presentation I have uploaded our business car design (logo and contact details ) and a current powerpoint template we are currently working with. Also a brief of how we operateOur mantra is Discover, Develop, Deliver.

Target Market(s)

multinationals and mid size SME's requiring help to grown new markets or geographies for their business.

Colors
000000

Requirements
Must have
• the mantra..our phases of engagement around assisting clients is:
• 1. Discover
• 2. Develop
• 3. Deliver
Nice to have
• we differentiate ourselves form consultant by actually executing the plan for them (i.e. is the delivery phase)

```html
<!DOCTYPE html>
<html lang="en">
<head>
<meta charset="UTF-8">
<title>Quellbrook Market Counsel – Email Signature</title>
<link rel="stylesheet" href="https://fonts.googleapis.com/css2?family=Montserrat:wght@500;600&display=swap">
<style>
  :root {
    --page-bg: #ffffff;
    --signature-bg: #022a3c;
    --accent-blue: #1d92c4;
    --text-light: #ffffff;
    --peak-light: #3a6880;
    --peak-dark: #2e5673;
  }
  * { box-sizing: border-box; margin: 0; padding: 0; }
  html, body {
    width: 1200px;
    height: 1200px;
    overflow: hidden;
    background: var(--page-bg);
    font-family: "Montserrat", sans-serif;
  }
  .signature {
    position: absolute;
    left: 50px;
    top: 455px;
    width: 1100px;
    height: 290px;
    background: var(--signature-bg);
    overflow: hidden;
  }
  .signature__scenery {
    position: absolute;
    left: 0;
    bottom: 0;
    width: 310px;
    height: 250px;
    background: linear-gradient(90deg, var(--peak-light), var(--peak-dark));
  }
  .signature__brand {
    position: absolute;
    left: 328px;
    top: 82px;
    width: 140px;
    display: flex;
    flex-direction: column;
    align-items: flex-start;
    gap: 10px;
  }
  .brand__square {
    width: 18px;
    height: 18px;
    background: var(--accent-blue);
  }
  .brand__name {
    color: var(--text-light);
    font-weight: 600;
    font-size: 19px;
    line-height: 1.2;
    letter-spacing: 0.04em;
    text-transform: uppercase;
  }
  .signature__person {
    position: absolute;
    left: 504px;
    top: 66px;
  }
  .person__name {
    color: var(--accent-blue);
    font-weight: 500;
    font-size: 26px;
    letter-spacing: 0.02em;
    text-transform: uppercase;
    line-height: 1.1;
  }
  .person__role {
    color: var(--text-light);
    font-weight: 500;
    font-size: 16px;
    letter-spacing: 0.03em;
    margin-top: 4px;
  }
  .signature__contacts {
    position: absolute;
    left: 817px;
    top: 173px;
    list-style: none;
  }
  .contact {
    display: flex;
    align-items: center;
    height: 28.5px;
    color: var(--text-light);
    font-size: 16px;
    font-weight: 500;
  }
  .contact__icon {
    width: 16px;
    height: 16px;
    margin-right: 16px;
    flex: none;
  }
</style>
</head>
<body>
  <section class="signature">
    <div class="signature__scenery" role="img" aria-label="Mountain range illustration in layered blue tones"></div>

    <div class="signature__brand">
      <span class="brand__square"></span>
      <span class="brand__name">Quellbrook<br>Market<br>Counsel</span>
    </div>

    <div class="signature__person">
      <p class="person__name">Mara Lindqvist</p>
      <p class="person__role">PRINCIPAL</p>
    </div>

    <ul class="signature__contacts">
      <li class="contact">
        <svg class="contact__icon" viewBox="0 0 16 16" aria-hidden="true">
          <path d="M10 2 L7.5 3 Q4 8 7 14 L9.5 14.5 L10.3 12 L8.6 11.2 Q7.2 8 8.8 5 L10.7 4.6 Z" fill="var(--accent-blue)"/>
        </svg>
        555-014-2273
      </li>
      <li class="contact">
        <svg class="contact__icon" viewBox="0 0 16 16" aria-hidden="true">
          <rect x="1" y="3.5" width="14" height="9" fill="var(--accent-blue)"/>
          <path d="M1 3.5 L8 9 L15 3.5 M1 12.5 L6 8 M15 12.5 L10 8" stroke="var(--signature-bg)" stroke-width="1.1" fill="none"/>
        </svg>
        m.lindqvist@quellbrook.ca
      </li>
      <li class="contact">
        <svg class="contact__icon" viewBox="0 0 16 16" aria-hidden="true">
          <g fill="none" stroke="var(--accent-blue)" stroke-width="1.3">
            <circle cx="8" cy="8" r="6.5"/>
            <ellipse cx="8" cy="8" rx="3" ry="6.5"/>
            <path d="M1.5 8 H14.5 M2.5 4.8 H13.5 M2.5 11.2 H13.5"/>
          </g>
        </svg>
        www.quellbrook.ca
      </li>
    </ul>
  </section>
</body>
</html>
```